Kelvor Engineers: Why you should hire us keepsake

New design. Open to plastic cards. We are an engineering firm that designs cell phone towers and commercial buildings. Please check out our website www.kelvorstruct.com for more details. We want people to remember our card and for it to be useful if possible. We want the same look and feel on these cards to be translated to other marketing material we may need such as brochures.

Target Market(s)

Architects, Developers and Telecommunication Carriers

Industry/Entity Type

Engineering

Contact Information for Business Card

Card with our company colors, logo, and innovative design with elements related to our industry.

Font styles to use
Sans Serif

Colors
9bcb3c
abd036
0255a3

Requirements
Must have
• Sleek and hip design
Nice to have
• Bright lime green and navy coloring that pops with an innovative design.
Should not have
• A basic and boring design

```html
<!DOCTYPE html>
<html lang="en">
<head>
<meta charset="utf-8">
<title>Kelvor Engineers – Business Card</title>
<link rel="stylesheet" href="https://fonts.googleapis.com/css2?family=Archivo:wght@400;500;600;700;800&display=swap">
<style>
  :root {
    --navy: #1c335f;
    --lime: #ccd52c;
    --white: #ffffff;
    --stage: #e4e6ea;
  }
  * { margin: 0; padding: 0; box-sizing: border-box; }
  html, body {
    width: 1200px; height: 900px; overflow: hidden;
    background: var(--stage);
    font-family: "Archivo", sans-serif;
  }
  .canvas { position: relative; width: 1200px; height: 900px; }

  .card {
    position: absolute; left: 300px;
    width: 600px; height: 343px;
    border-radius: 18px; overflow: hidden;
    background: var(--navy);
    box-shadow: 0 10px 30px rgba(20, 30, 50, 0.18);
  }
  .card--front { top: 86px; }
  .card--back  { top: 471px; }

  /* front */
  .front-name {
    position: absolute; left: 0; right: 0; top: 112px;
    text-align: center;
    font-weight: 800; font-size: 50px; letter-spacing: -1px;
    color: var(--lime);
  }
  .front-name .mark {
    display: inline-block; width: 22px; height: 22px;
    background: var(--lime); margin-right: 14px; vertical-align: 4px;
  }
  .cities {
    position: absolute; left: 0; right: 0; top: 216px;
    text-align: center;
    font-weight: 600; font-size: 15px; letter-spacing: 2.5px;
    color: var(--white); text-transform: uppercase;
  }
  .cities .sep { color: var(--lime); margin: 0 8px; }

  /* back */
  .back-shape { position: absolute; inset: 0; }
  .back-brand { position: absolute; left: 36px; top: 34px; }
  .back-brand .name {
    font-weight: 800; font-size: 34px; letter-spacing: -0.5px;
    color: var(--lime);
  }
  .back-brand .tagline {
    margin-top: 6px;
    font-weight: 500; font-size: 12px; letter-spacing: 1.6px;
    color: var(--white); text-transform: uppercase;
  }
  .contact-block {
    position: absolute; right: 48px; top: 180px;
    text-align: right; color: var(--navy);
  }
  .person { font-weight: 700; font-size: 21px; }
  .role { font-weight: 400; font-size: 15px; color: var(--lime); margin-top: 2px; }
  .details { list-style: none; margin-top: 12px; }
  .details li {
    font-size: 14px; line-height: 21px;
    display: flex; justify-content: flex-end; align-items: center; gap: 10px;
  }
  .details svg { width: 11px; height: 11px; flex: none; }
  .accent-bar {
    position: absolute; right: 0; top: 186px;
    width: 14px; height: 42px; display: flex;
  }
  .accent-bar span:first-child { width: 5px; background: var(--lime); }
  .accent-bar span:last-child { flex: 1; background: var(--navy); }
</style>
</head>
<body>
<main class="canvas">

  <section class="card card--front" aria-label="Card front">
    <div class="front-name"><span class="mark"></span>Kelvor Engineers</div>
    <div class="cities">Atlanta<span class="sep">/</span>Charlotte<span class="sep">/</span>Houston<span class="sep">/</span>San Antonio</div>
  </section>

  <section class="card card--back" aria-label="Card back">
    <svg class="back-shape" viewBox="0 0 600 343" preserveAspectRatio="none">
      <polygon points="232,152 600,152 600,343 292,343" fill="#ffffff"/>
    </svg>

    <div class="back-brand">
      <div class="name">Kelvor Engineers</div>
      <div class="tagline">Multi-Discipline Engineering</div>
    </div>

    <div class="contact-block">
      <div class="person">Dana Holloway Pryce</div>
      <div class="role">Director</div>
      <ul class="details">
        <li>555.014.7031
          <svg viewBox="0 0 12 12"><path d="M3 1 L5 3.5 L4 5 Q5 7 7 8 L8.5 7 L11 9 L9.5 11 Q4 10.5 1 3 Z" fill="none" stroke="#ccd52c" stroke-width="1.2"/></svg>
        </li>
        <li>555.019.4468
          <svg viewBox="0 0 12 12"><rect x="3" y="0.8" width="6" height="10.4" rx="1" fill="none" stroke="#ccd52c" stroke-width="1.2"/><circle cx="6" cy="9.3" r="0.7" fill="#ccd52c"/></svg>
        </li>
        <li>dpryce@kelvorstruct.com
          <svg viewBox="0 0 12 12"><rect x="0.8" y="2.5" width="10.4" height="7" fill="none" stroke="#ccd52c" stroke-width="1.2"/><path d="M1 3 L6 6.8 L11 3" fill="none" stroke="#ccd52c" stroke-width="1.2"/></svg>
        </li>
        <li>www.kelvorstruct.com
          <svg viewBox="0 0 12 12"><circle cx="6" cy="6" r="5" fill="none" stroke="#ccd52c" stroke-width="1.1"/><ellipse cx="6" cy="6" rx="2.2" ry="5" fill="none" stroke="#ccd52c" stroke-width="1"/><path d="M1 6 H11 M2 3.5 H10 M2 8.5 H10" stroke="#ccd52c" stroke-width="0.9"/></svg>
        </li>
      </ul>
    </div>

    <div class="accent-bar"><span></span><span></span></div>
  </section>

</main>
</body>
</html>
```